Velmoscu theartres special events brochure

Design a brochure for our special events being held at the Dulvane and Prask Theatres from Dec - March

I wanted to limit the pages - but seeing the designs come in i think it will have to be a total of eight pages which would be 2 (8 1/2 by 11 inch) paper folded in half. This includes the cover and back cover.
pages as:
1) cover
2) inside cover (page 1)
3)page 2 (right of inside cover)
4) page 3 (middle left)
5) page 4 (middle right)
6) page 5 (left of back inside cover)
7) page 6 (back inside cover)
8) Back cover

Hope this helps

We have an old audience so text should not be too small (at least 12-14 pt)

Each special event is listed in the Word document. titled : January to March 2017 Velmoscu Theatre events Final

Velmoscu Theatre is the company - the two theaters are the Prask and Dulvane

Target Market(s)

Movie - comedy - live music goers

Industry/Entity Type

Movie Theater

Font styles to use
Serif

Requirements
Must have
• cool style and layout
• A photo for each event is attached and must be included for each event.
Should not have
• clip art

```html
<!DOCTYPE html>
<html lang="en">
<head>
<meta charset="utf-8">
<title>Velmoscu Theatres – Special Events, Page 3</title>
<link href="https://fonts.googleapis.com/css2?family=Arimo:wght@400;700&family=Libre+Baskerville:ital,wght@0,400;0,700;1,700&family=Tinos:wght@400;700&display=swap" rel="stylesheet">
<style>
  :root {
    --sky: #1fa3dc;
    --sky-pale: #bfe6f7;
    --violet: #3b2a8f;
    --gold: #f6c62d;
    --ink: #1d1d1f;
    --paper: #ffffff;
    --date-ink: #3b2a8f;
  }
  * { box-sizing: border-box; margin: 0; padding: 0; }
  html, body { width: 804px; height: 1200px; overflow: hidden; background: var(--paper); }
  .page { position: relative; width: 804px; height: 1200px; background: var(--paper); }
  .sidebar {
    position: absolute; left: 28px; top: 34px; width: 756px; height: 1140px;
    background: var(--sky);
  }
  .panel {
    position: absolute; left: 266px; top: 74px; width: 518px; height: 1100px;
    background: var(--paper); overflow: hidden;
  }
  .ticket-tag {
    position: absolute; left: 61px; width: 190px; height: 60px;
    background: var(--violet); border: 2px solid var(--paper);
    border-radius: 12px 0 12px 0;
    font-family: "Libre Baskerville", Georgia, serif; font-style: italic; font-weight: 700;
    text-align: center; line-height: 1;
    color: var(--paper); font-size: 24px; padding-top: 4px;
  }
  .ticket-tag .price { color: var(--gold); display: block; }
  .photo { position: absolute; border: 3px solid var(--paper); }
  .photo-portrait { left: 74px; top: 165px; width: 158px; height: 241px;
    background: linear-gradient(160deg, #9a9a9a, #3a3a3a 60%, #1c1c1c); }
  .photo-poster { left: 68px; top: 590px; width: 168px; height: 261px;
    background: linear-gradient(180deg, #f4f1ea 0 30%, #c7c2b4 30%, #8e8a80); }
  .event { position: absolute; left: 0; width: 518px; padding: 0 14px 0 8px; }
  .event-first { top: 14px; }
  .event-second { top: 470px; }
  .banner { display: block; width: 500px; height: 46px; }
  .banner-title {
    font-family: "Libre Baskerville", Georgia, serif; font-weight: 700;
    font-size: 22px; fill: var(--paper);
  }
  .event-date {
    font-family: "Arimo", Arial, sans-serif; font-size: 16px; color: var(--date-ink);
    margin: 4px 0 8px 22px;
  }
  .event-date strong { color: var(--ink); font-weight: 400; }
  .event-body {
    font-family: "Tinos", "Times New Roman", serif; font-size: 18px; line-height: 19.5px;
    color: var(--ink); margin-left: 22px; position: relative; z-index: 1;
  }
  .event-body p + p { margin-top: 18px; }
  .event-body sup { font-size: 10px; line-height: 0; }
  .showtimes { margin-top: 22px; }
  .skyline {
    position: absolute; left: 0; bottom: 0; width: 100%; height: 130px;
    background: linear-gradient(180deg, rgba(191,230,247,0) 0%, var(--sky-pale) 55%, var(--sky) 100%);
  }
</style>
</head>
<body>
<main class="page">
  <div class="sidebar"></div>

  <div class="ticket-tag" style="top:70px">Tickets are<span class="price">$15</span></div>
  <div class="photo photo-portrait" role="img" aria-label="Black and white studio portrait of actress Marla Vennick"></div>

  <div class="ticket-tag" style="top:518px">Tickets are<span class="price">$20</span></div>
  <div class="photo photo-poster" role="img" aria-label="Poster for Ballot Box Giggles with Gil Haverty"></div>

  <section class="panel">
    <div class="skyline" role="img" aria-label="Decorative light blue silhouette of film and stage motifs"></div>

    <article class="event event-first">
      <svg class="banner" viewBox="0 0 500 46" aria-label="Laurel Evening with Marla Vennick">
        <rect x="22" y="3" width="456" height="40" fill="var(--violet)"/>
        <rect x="26" y="7" width="448" height="32" fill="none" stroke="var(--paper)" stroke-width="1.5"/>
        <path d="M2 23h14M8 15v16M498 23h-14M492 15v16" stroke="var(--violet)" stroke-width="4"/>
        <text class="banner-title" x="250" y="31" text-anchor="middle">Laurel Evening with Marla Vennick</text>
      </svg>
      <p class="event-date">January 14 – Dulvane Theatre</p>
      <div class="event-body">
        <p>Marla Vennick graced the silver screen for over 60 years. Ms. Vennick is a three time Laurel Nominee for her outstanding performances in The Long Table (1958), Evening Tide (1973) and A Quiet Harbor (1984). She received a Silver Lantern in 1993 for her television role as Ada Pell in the cult favorite, Lantern Creek. The event will showcase two of Ms. Vennick’s Laurel nominated films and a Q &amp; A after each movie. Ms. Vennick will also be inducted into the Silver Reel Hall of Fame. The Laurel Series is part of the 20<sup>th</sup> Anniversary yearlong celebration of the Coastal Independent Film Festival.</p>
        <p class="showtimes">2PM - A Quiet Harbor<br>5PM - Evening Tide<br>8PM - The Long Table</p>
      </div>
    </article>

    <article class="event event-second">
      <svg class="banner" viewBox="0 0 500 46" aria-label="Live at the Dulvane Theatre">
        <rect x="22" y="3" width="456" height="40" fill="var(--violet)"/>
        <rect x="26" y="7" width="448" height="32" fill="none" stroke="var(--paper)" stroke-width="1.5"/>
        <path d="M2 23h14M8 15v16M498 23h-14M492 15v16" stroke="var(--violet)" stroke-width="4"/>
        <text class="banner-title" x="250" y="31" text-anchor="middle">Live at the Dulvane Theatre</text>
      </svg>
      <p class="event-date"><strong>Ballot Box Giggles</strong> with Gil Haverty – January 19, 8PM</p>
      <div class="event-body">
        <p>The laughs continue on inauguration day with Ballot Box Giggles: 2016 with Gil Haverty. This is a new, hysterical, show about one-man stalking the presidential election cycle. Ably assisted by his trusty overhead projector, this hilarious 90-minute production reflects Haverty’s outraged and outrageous sensibilities, accessing the topical through the jugular, as current as Norma Quillfeather’s lead staffer’s latest tweet.</p>
        <p>Ambrose Kettleby called the American political process a circus wrapped inside a game show covered in poisonous weasel glitter. Well, he should have. And both sides of the partisan aisle can’t help but agree that the 2016 election season has spawned one of the most fertile, febrile and fecund campaigns in history. For mocking and scoffing and taunting purposes, that is. As a source for comedic material it has been an embarrassment of riches. Lush like a tropical rain forest. A cornucopia of delights, like slam- dunking from a step- ladder.</p>
        <p>Co-authored by the best joke writers in the business: Otto Brandvik, Celia Marsh, Linus Okafor, Ruthanne</p>
      </div>
    </article>
  </section>
</main>
</body>
</html>
```